Law Offices business card

Hi there, I'll need business card for the Law Offices of Colin Matheny. The information must convey his strategic approach and quick resolution to complex business litigation needs. Please emphasize Civil Litigation, Corporate Law, Business Governance and Real Estate Law. Colin has over 25 years of experience in these fields.The card should be modern and edgy and the message should be clear. Please consult his current website for ideas.

```html
<!DOCTYPE html>
<html lang="en">
<head>
<meta charset="utf-8">
<title>Law Offices of Colin Matheny – Business Card</title>
<link rel="stylesheet" href="https://fonts.googleapis.com/css2?family=Arimo:wght@400;700&display=swap">
<style>
  :root {
    --stage: #3a3a3c;
    --card-red: #c24f4e;
    --card-black: #0c0c0d;
    --band-dark: #6e1c1c;
    --ink-white: #ffffff;
    --ink-soft: #d9d9d9;
    --ink-black: #111111;
    --accent: #c24f4e;
  }
  * { box-sizing: border-box; margin: 0; padding: 0; }
  html, body {
    width: 1200px; height: 950px; overflow: hidden;
    background: var(--stage);
    font-family: "Arimo", Arial, sans-serif;
  }
  .stage { position: relative; width: 1200px; height: 950px; }
  .card {
    position: absolute; left: 250px; width: 700px; height: 400px;
    overflow: hidden;
  }

  /* Front */
  .card--front { top: 60px; background: var(--card-red); }
  .front-mark {
    position: absolute; left: 0; right: 0; top: 150px;
    display: flex; align-items: center; justify-content: center; gap: 12px;
    color: var(--ink-white); font-weight: 700; font-size: 30px; letter-spacing: 1px;
  }
  .front-mark__square { width: 18px; height: 18px; background: var(--ink-white); }
  .front-web {
    position: absolute; left: 0; right: 0; top: 262px;
    display: flex; align-items: center; justify-content: center; gap: 14px;
    color: var(--ink-white); font-size: 15px; letter-spacing: 4px;
  }
  .front-web__rule { width: 70px; height: 1px; background: var(--ink-white); }

  /* Back */
  .card--back { top: 490px; background: var(--card-black); }
  .name-band {
    position: absolute; left: 0; top: 150px; width: 330px; height: 80px;
    background: var(--card-red);
  }
  .name-band__edge {
    position: absolute; left: 330px; top: 96px; width: 8px; height: 80px;
    background: var(--band-dark);
  }
  .person { position: absolute; left: 60px; top: 168px; color: var(--ink-black); }
  .person__name { font-size: 20px; font-weight: 700; line-height: 1.2; }
  .person__title { font-size: 15px; margin-top: 3px; }

  .firm { position: absolute; left: 352px; top: 70px; color: var(--ink-white); }
  .firm__pre { font-size: 15px; font-weight: 700; letter-spacing: 1px; }
  .firm__name { font-size: 38px; font-weight: 700; line-height: 1.08; margin-top: 6px; }

  .address {
    position: absolute; right: 40px; top: 220px; text-align: right;
    font-style: normal;
    color: var(--ink-soft); font-size: 15px; line-height: 1.45; letter-spacing: .5px;
  }
  .contacts {
    position: absolute; left: 140px; top: 268px; list-style: none;
    color: var(--ink-soft); font-size: 16px;
  }
  .contacts li { display: flex; align-items: center; gap: 10px; height: 24px; }
  .contacts svg { width: 14px; height: 14px; fill: var(--accent); }
</style>
</head>
<body>
<main class="stage">
  <section class="card card--front" aria-label="Card front">
    <div class="front-mark"><span class="front-mark__square"></span>Colin Matheny</div>
    <div class="front-web"><span class="front-web__rule"></span>www.mathenylaw.com<span class="front-web__rule"></span></div>
  </section>

  <section class="card card--back" aria-label="Card back">
    <div class="name-band"></div>
    <div class="name-band__edge"></div>
    <div class="person">
      <p class="person__name">Evan Marlow</p>
      <p class="person__title">President</p>
    </div>
    <div class="firm">
      <p class="firm__pre">LAW OFFICES OF</p>
      <p class="firm__name">Colin<br>Matheny, PA</p>
    </div>
    <address class="address">
      2710 Harbor Crest Lane<br>
      Larkfield, NY 11720<br>
      www.mathenylaw.com
    </address>
    <ul class="contacts">
      <li><svg viewBox="0 0 16 16" aria-hidden="true"><path d="M2 5c0-2 2-3 6-3s6 1 6 3v2h-3V5.5H5V7H2z M4 8h8l2 6H2z"/></svg>412 555 0187</li>
      <li><svg viewBox="0 0 16 16" aria-hidden="true"><path d="M4 1h8v14H4z M5.5 3v9h5V3z"/></svg>412 555 0243</li>
      <li><svg viewBox="0 0 16 16" aria-hidden="true"><path d="M4 1h8v4H4z M1 6h14v7h-3v2H4v-2H1z M5 10v4h6v-4z"/></svg>412 555 0396</li>
      <li><svg viewBox="0 0 16 16" aria-hidden="true"><path d="M1 3h14v10H1z M2 4l6 5 6-5v-.2H2z" fill-rule="evenodd"/></svg>evan@mathenylaw.com</li>
    </ul>
  </section>
</main>
</body>
</html>
```